Business Card - high end, modern health care

Hey designers!

We need a double sided business card for the boutique, cutting edge physical therapy rehabilitation centre in Sydney's Northern Beaches.

With the most qualified physios in the area The Harbourview Motion Clinic does what other physiotherapy practices do not, we take our time with our patients giving them longer appointments, better physios and therefor faster results!

We guarantee that the service people receive at THMC will be unparalleled.

Hence we need a business card to reflect our modern, boutique, high end service. The final design needs to reflect that we are in a class of our own yet with the feel of beachside retreat.

Below I have attached our logo in both blue on white and white on blue. The exact colour is;
and the font that we have used in our logo is Tex Gyre Aventador.

I like the idea of the blue as the main colour as it is more eye catching and our signage onto the main road will be in this blue and in the interest of consistency across marketing the blue needs to be a part of the design. However I would appreciate a few designs onto a wooden background as this is a visual theme within the fitout of the practice.

The design needs to be of standard size (91x55mm).

Target Market(s)

We target people who have an end outcome in mind and those who have had poor experiences with other providers and ensure that everyone gets the care that they deserve with a premium service that is tailored to the individuals circumstances. As a premium service, the target market is highly educated, business and tech savvy with the additional target market of elderly people who have self funded their retirement and see value in paying for the best ongoing rehabilitation to maintain independence.

Industry/Entity Type

Physical Therapy

Contact Information for Business Card

Name, designation( Titled Musculoskeletal Physiotherapist... there will also be those in the company that have multiple designations ie 5 or 6 words long), phone number, email, facebook, instagram, address

Font styles to use
Sans Serif

Colors

Designer to choose colors to be used in the design.

Requirements
Must have
• Front - The logo as large as possible, blue or wooden theme, and all of the important details.
• Back - A blank space/lines on which to write appointment times (no "Appointment, date, time" etc.)
Nice to have
• facebook url
• logos for facebook and instagram
• Mini logos for the phone and email?

```html
<!DOCTYPE html>
<html lang="en">
<head>
<meta charset="UTF-8">
<title>The Harbourview Motion Clinic — Business Card</title>
<link href="https://fonts.googleapis.com/css2?family=Poppins:wght@300;400;600&display=swap" rel="stylesheet">
<style>
  :root {
    --brand-blue: #0b4f9f;
    --brand-blue-deep: #083f84;
    --paper: #ffffff;
    --paper-shade: #eef0f3;
    --rule: #9aa3ad;
    --backdrop: #d9dcdf;
    --card-w: 520px;
    --card-h: 314px;
  }
  * { box-sizing: border-box; margin: 0; padding: 0; }
  html, body {
    width: 1200px; height: 900px; overflow: hidden;
    background: var(--backdrop);
    font-family: "Poppins", sans-serif;
  }
  .sheet {
    width: 1200px; height: 900px;
    display: flex; align-items: center; justify-content: center; gap: 48px;
  }
  .card {
    position: relative;
    width: var(--card-w); height: var(--card-h);
    border-radius: 22px;
    overflow: hidden;
    box-shadow: 0 10px 28px rgba(0,0,0,0.18);
  }

  /* Front */
  .card--front {
    background: linear-gradient(160deg, var(--brand-blue) 0%, var(--brand-blue-deep) 100%);
    color: var(--paper);
  }
  .contact { position: absolute; left: 28px; top: 28px; }
  .contact__name {
    font-size: 20px; font-weight: 600; letter-spacing: 0.5px;
    text-transform: uppercase; line-height: 1.1;
  }
  .contact__role { font-size: 11px; font-weight: 300; margin-top: 2px; }
  .contact__address { font-size: 11px; font-weight: 400; line-height: 1.45; margin-top: 20px; }
  .contact__list { list-style: none; margin-top: 16px; font-size: 10.5px; line-height: 1.7; }
  .contact__list li { display: flex; align-items: center; gap: 7px; }
  .contact__list svg { width: 10px; height: 10px; flex: none; }

  .emblem-field {
    position: absolute; left: 0; top: 0; width: 100%; height: 100%;
  }
  .brand-lockup {
    position: absolute; left: 275px; top: 120px; width: 220px;
    display: flex; flex-direction: column; align-items: center;
    color: var(--brand-blue);
  }
  .brand-lockup__dot {
    width: 74px; height: 74px; border-radius: 50%;
    background: var(--brand-blue);
  }
  .brand-lockup__name {
    margin-top: 14px; text-align: center;
    font-size: 17px; font-weight: 600; line-height: 1.2;
    letter-spacing: 1px; text-transform: uppercase;
  }

  /* Back */
  .card--back { background: linear-gradient(180deg, var(--paper) 0%, var(--paper-shade) 100%); }
  .back__band {
    position: absolute; left: 0; top: 0; width: 100%; height: 128px;
    background: linear-gradient(160deg, var(--brand-blue) 0%, var(--brand-blue-deep) 100%);
    display: flex; align-items: center; gap: 14px; padding: 0 30px;
    color: var(--paper);
  }
  .back__dot { width: 34px; height: 34px; border-radius: 50%; background: var(--paper); flex: none; }
  .back__name {
    font-size: 18px; font-weight: 600; letter-spacing: 1px;
    text-transform: uppercase; line-height: 1.2;
  }
  .back__label {
    position: absolute; right: 34px; top: 146px;
    font-size: 15px; font-weight: 300; color: var(--brand-blue); letter-spacing: 0.5px;
  }
  .back__lines { position: absolute; left: 34px; right: 34px; top: 196px; }
  .back__lines span { display: block; height: 1px; background: var(--rule); margin-bottom: 34px; }
</style>
</head>
<body>
<main class="sheet">

  <section class="card card--front" aria-label="Business card front">
    <svg class="emblem-field" viewBox="0 0 520 314" aria-hidden="true">
      <circle cx="385" cy="250" r="176" fill="#ffffff"/>
      <path d="M 198 300 A 192 192 0 0 1 400 58" fill="none" stroke="#ffffff" stroke-width="4" stroke-linecap="round"/>
    </svg>

    <div class="contact">
      <h1 class="contact__name">Daniel Reeve</h1>
      <p class="contact__role">Director</p>
      <p class="contact__address">48 Ocean Parade, Unit 3,<br>Dee Why NSW 2099</p>
      <ul class="contact__list">
        <li>
          <svg viewBox="0 0 10 10"><path d="M2 0.8 L3.6 0.8 L4.2 3 L3 3.8 Q4 6 6.2 7 L7 5.8 L9.2 6.4 L9.2 8 Q9.2 9.2 8 9.2 Q0.8 8.6 0.8 2 Q0.8 0.8 2 0.8Z" fill="#fff"/></svg>
          +61 2 9982 4417
        </li>
        <li>
          <svg viewBox="0 0 10 10"><rect x="0.6" y="2" width="8.8" height="6" fill="none" stroke="#fff" stroke-width="1"/><path d="M0.6 2 L5 5.6 L9.4 2" fill="none" stroke="#fff" stroke-width="1"/></svg>
          info@harbourview.clinic
        </li>
        <li>
          <svg viewBox="0 0 10 10"><circle cx="5" cy="5" r="4.3" fill="none" stroke="#fff" stroke-width="1"/><ellipse cx="5" cy="5" rx="1.8" ry="4.3" fill="none" stroke="#fff" stroke-width="0.8"/><path d="M0.7 5 H9.3" stroke="#fff" stroke-width="0.8"/></svg>
          www.harbourview.clinic
        </li>
      </ul>
    </div>

    <div class="brand-lockup">
      <span class="brand-lockup__dot"></span>
      <p class="brand-lockup__name">The Harbourview<br>Motion Clinic</p>
    </div>
  </section>

  <section class="card card--back" aria-label="Business card back">
    <div class="back__band">
      <span class="back__dot"></span>
      <p class="back__name">The Harbourview<br>Motion Clinic</p>
    </div>
    <p class="back__label">Appointment</p>
    <div class="back__lines"><span></span><span></span><span></span></div>
  </section>

</main>
</body>
</html>
```